Real Estate Webpage Design

We have an existing website: ferndaleestatecollective.com.au
We focus customised service mainly on Property Management and second-hand property sales.
We are not entirely happy about the current design and layout can stay roughly the same as the back end coding is linked to a CRM system.
We would like to see the design are more reachable to our clients and appearing.
Please check our Website Design Draft for more details.

Industry/Entity Type

Real estate Agency

Number of Pages Required

5+ page

Font styles to use
Sans Serif

Colors

Designer to choose colors to be used in the design.

```html
<!DOCTYPE html>
<html lang="en">
<head>
<meta charset="utf-8">
<title>Ferndale Estate Collective — Home</title>
<link href="https://fonts.googleapis.com/css2?family=Poppins:ital,wght@0,300;0,400;0,500;0,600;1,400&display=swap" rel="stylesheet">
<style>
:root{
  --navy:#1b3358;
  --gold:#ecbd4f;
  --cream:#fbf3e3;
  --ink:#222a36;
  --muted:#6f7580;
  --line:#e4e6ea;
  --white:#fff;
}
*{box-sizing:border-box;margin:0;padding:0}
html,body{width:1200px;height:3889px;overflow:hidden}
body{position:relative;font-family:'Poppins',sans-serif;color:var(--ink);background:var(--white)}
.abs{position:absolute}
.btn{position:absolute;background:var(--gold);color:var(--white);font-size:13px;display:flex;align-items:center;justify-content:center;border-bottom:2px solid #d6a53a;white-space:nowrap}
.h2{font-weight:500;font-size:27px;color:var(--ink)}
/* hero */
.hero{left:0;top:0;width:1200px;height:575px;background:linear-gradient(100deg,#e9eaea 0%,#d9dbdb 40%,#c7c9c9 70%,#e3e4e4 100%)}
.brand{left:60px;top:14px;display:flex;align-items:center;gap:12px}
.brand .mark{width:56px;height:56px;border:3px solid var(--gold)}
.brand .name{font-size:38px;font-weight:500;color:var(--navy);line-height:1}
.brand .sub{font-size:11px;color:var(--navy);letter-spacing:1px;margin-top:4px}
.nav{left:436px;top:28px;width:552px;display:flex;justify-content:space-between;font-size:13.5px;color:var(--ink);white-space:nowrap}
.hero-title{left:60px;top:190px;width:620px;font-size:38px;font-weight:500;line-height:50px;color:var(--navy)}
.hero-title span{color:var(--gold)}
.hero-copy{left:60px;top:300px;width:540px;font-size:13px;line-height:22px;color:var(--muted)}
/* search */
.search{left:60px;top:575px;width:1080px;height:90px;background:var(--white);box-shadow:0 4px 14px rgba(0,0,0,.08)}
.field{position:absolute;top:22px}
.field b{display:block;font-weight:500;font-size:14px}
.field span{display:block;font-size:12px;color:var(--muted);margin-top:10px}
.field svg{position:absolute;right:-6px;top:40px}
.divider{position:absolute;top:22px;width:1px;height:56px;background:var(--line)}
.search-go{left:1007px;top:21px;width:56px;height:54px;background:var(--gold);display:flex;align-items:center;justify-content:center}
/* about */
.feature{width:185px;height:160px;background:var(--white);box-shadow:0 2px 12px rgba(0,0,0,.07);display:flex;flex-direction:column;align-items:center;justify-content:center;text-align:center;font-size:16px;line-height:24px;font-weight:500}
.feature svg{margin-bottom:14px}
.kicker{font-size:12px;color:var(--gold)}
.copy{font-size:13px;line-height:22px;color:var(--muted)}
/* agents */
.agents{left:0;top:1166px;width:1200px;height:434px;background:var(--cream)}
.portrait{position:absolute;background:linear-gradient(180deg,#d7d9dc,#9aa0a8 60%,#2a2f3a);}
/* listings */
.tab{position:absolute;top:1753px;height:37px;border:1.5px solid var(--ink);font-size:13px;display:flex;align-items:center;justify-content:center;background:var(--white)}
.tab.on{background:var(--gold);border-color:var(--gold);color:var(--white)}
.card{position:absolute;top:1829px;width:340px;height:389px;background:var(--white);box-shadow:0 2px 12px rgba(0,0,0,.08)}
.card-head{height:44px;background:var(--navy);color:var(--white);padding:4px 0 0 66px;font-size:12px;line-height:17px;position:relative;white-space:nowrap}
.card-head b{font-weight:600;font-size:13px}
.card-photo{height:185px;position:relative}
.price{position:absolute;left:12px;bottom:14px;color:var(--white);font-weight:600;font-size:16px}
.card-specs{position:absolute;left:20px;top:250px;display:flex;gap:22px;font-size:13px}
.card .ins{position:absolute;left:20px;top:280px;font-size:16px;font-weight:500}
.card .date{position:absolute;left:20px;top:307px;font-size:13px;color:var(--gold)}
.card .foot{position:absolute;left:0;top:344px;width:340px;border-top:1px solid var(--line);height:45px;display:flex;align-items:center;padding:0 20px;font-size:13px;gap:10px}
.avatar{width:30px;height:30px;background:#8d939c}
/* testimonial */
.quotes{left:0;top:2381px;width:1200px;height:374px;background:var(--navy)}
.arrow{position:absolute;top:2565px;width:33px;height:32px;display:flex;align-items:center;justify-content:center}
/* news */
.news-photo{position:absolute;width:225px;height:145px}
.meta{position:absolute;font-size:12px;color:var(--muted)}
.news-title{position:absolute;font-size:17px;line-height:26px;font-weight:500;width:270px}
.read{position:absolute;font-size:13px;color:var(--gold)}
/* cta & footer */
.cta{left:0;top:3315px;width:1200px;height:227px;background:var(--gold)}
.footer{left:0;top:3542px;width:1200px;height:347px;background:var(--navy);color:var(--white)}
.footer h4{position:absolute;font-size:14px;font-weight:500;color:var(--gold)}
.footer ul{position:absolute;list-style:none;font-size:12px}
.footer li{height:26.7px}
.footer li::before{content:"⟶ ";}
.social{position:absolute;top:3627px;width:38px;height:38px;border-radius:50%;border:1.5px solid var(--white)}
</style>
</head>
<body>

<!-- Hero -->
<section class="abs hero" role="img" aria-label="Bright living room with a white sofa, plants and shelves"></section>
<div class="abs brand">
  <div class="mark"></div>
  <div><div class="name">Ferndale</div><div class="sub">Estate Collective</div></div>
</div>
<nav class="abs nav"><span>Home</span><span>About Us</span><span>Leasing</span><span>Buy</span><span>Sell</span><span>Our Team</span><span>Blog</span><span>Contact Us</span></nav>
<div class="btn" style="left:1012px;top:20px;width:128px;height:33px;">Add Properties</div>
<h1 class="abs hero-title">Welcome To <span>Ferndale</span> Estate Collective</h1>
<p class="abs hero-copy">Lorem Ipsum is simply dummy text of the printing and typesetting industry. Lorem Ipsum has been the industry's standard dummy text ever since the 1500s, when an unknown printer</p>
<div class="btn" style="left:60px;top:395px;width:150px;height:33px;">See All Properties</div>

<!-- Search -->
<div class="abs search">
  <div class="field" style="left:24px;width:195px"><b>Categories</b><span>Property Category</span><svg width="12" height="8" viewBox="0 0 12 8"><path d="M1 1l5 5 5-5" fill="none" stroke="#222" stroke-width="1.5"/></svg></div>
  <div class="divider" style="left:233px"></div>
  <div class="field" style="left:249px;width:150px"><b>City</b><span>Property City</span><svg width="12" height="8" viewBox="0 0 12 8"><path d="M1 1l5 5 5-5" fill="none" stroke="#222" stroke-width="1.5"/></svg></div>
  <div class="divider" style="left:414px"></div>
  <div class="field" style="left:436px;width:160px"><b>Area</b><span>Property Area</span><svg width="12" height="8" viewBox="0 0 12 8"><path d="M1 1l5 5 5-5" fill="none" stroke="#222" stroke-width="1.5"/></svg></div>
  <div class="divider" style="left:612px"></div>
  <div class="field" style="left:632px;width:160px"><b>Type</b><span>Apartment</span><svg width="12" height="8" viewBox="0 0 12 8"><path d="M1 1l5 5 5-5" fill="none" stroke="#222" stroke-width="1.5"/></svg></div>
  <div class="divider" style="left:803px"></div>
  <div class="field" style="left:823px;width:160px"><b>Price Range</b><span>1-50,00,000</span><svg width="12" height="8" viewBox="0 0 12 8"><path d="M1 1l5 5 5-5" fill="none" stroke="#222" stroke-width="1.5"/></svg></div>
  <div class="abs search-go"><svg width="24" height="24" viewBox="0 0 24 24"><circle cx="10" cy="10" r="7" fill="none" stroke="#fff" stroke-width="2"/><path d="M15 15l6 6" stroke="#fff" stroke-width="2"/></svg></div>
</div>

<!-- About -->
<div class="abs feature" style="left:60px;top:750px">
  <svg width="50" height="52" viewBox="0 0 50 52" fill="none" stroke="#1b3358" stroke-width="2"><rect x="6" y="4" width="30" height="42"/><path d="M12 30h18M12 36h18M12 42h12"/><circle cx="21" cy="16" r="5"/><circle cx="40" cy="10" r="6" stroke="#ecbd4f"/></svg>
  Great Experience</div>
<div class="abs feature" style="left:264px;top:750px">
  <svg width="56" height="50" viewBox="0 0 56 50" fill="none" stroke="#1b3358" stroke-width="2"><path d="M4 26l10-8 10 6 8-6 10 2 10 8M14 30l10 10 6-4 6 4 10-8"/><rect x="22" y="4" width="14" height="14" stroke="#ecbd4f"/></svg>
  Safety Deals</div>
<div class="abs feature" style="left:60px;top:928px">
  <svg width="52" height="52" viewBox="0 0 52 52" fill="none" stroke="#1b3358" stroke-width="2"><circle cx="24" cy="26" r="16"/><circle cx="24" cy="22" r="6"/><path d="M14 38c3-6 17-6 20 0"/><rect x="36" y="4" width="12" height="10" stroke="#ecbd4f"/></svg>
  Comprehensive<br>Support</div>
<div class="abs feature" style="left:264px;top:928px">
  <svg width="52" height="52" viewBox="0 0 52 52" fill="none" stroke="#1b3358" stroke-width="2"><path d="M4 44h10V30H4zM14 32h14l10-6 8 4-18 14H14"/><rect x="24" y="4" width="14" height="14" stroke="#ecbd4f"/></svg>
  Property<br>Management</div>

<div class="abs kicker" style="left:510px;top:759px">About Us</div>
<div class="abs h2" style="left:510px;top:781px">Who Is Ferndale?</div>
<p class="abs copy" style="left:510px;top:820px;width:490px">Ferndale Estate Collective grew from a simple idea: buying a home is one of the most expensive decisions and important assets for people. Ferndale is a real estate company located in Gungahlin, Canberra.</p>
<p class="abs copy" style="left:510px;top:898px;width:490px">Being a portfolio sales agent and property manager, coupled with our high–profile international real estate experience, Ferndale is considered a market leader on the cutting edge with deep industry knowledge, ranging from landlord–tenant relationships, residential purchases.</p>
<div class="abs" style="left:510px;top:998px;font-size:13px">Have question? Call us <span style="color:var(--gold);font-size:16px;margin-left:4px">02 6100 4821</span></div>
<div class="btn" style="left:510px;top:1050px;width:130px;height:32px">More About Us</div>

<!-- Agents -->
<section class="abs agents"></section>
<div class="abs h2" style="left:60px;top:1227px">Our Agents</div>
<p class="abs copy" style="left:60px;top:1296px;width:490px;color:var(--ink);font-size:13.5px;line-height:22.5px">Lorem Ipsum is simply dummy text of the printing and typesetting industry. Lorem Ipsum has been the industry's standard dummy text ever since the 1500s, when an unknown printer took a galley of type and scrambled it to make a type specimen book. It has survived not only five centuries, but also the leap into electronic typesetting, remaining essentially unchanged. It was popularised in the 1960s with the release of Letraset sheets.</p>
<div class="btn" style="left:60px;top:1497px;width:106px;height:32px">Our Agents</div>
<div class="portrait" style="left:712px;top:1251px;width:133px;height:127px" role="img" aria-label="Agent portrait"></div>
<div class="portrait" style="left:712px;top:1390px;width:133px;height:127px" role="img" aria-label="Agent portrait"></div>
<div class="portrait" style="left:860px;top:1281px;width:133px;height:127px" role="img" aria-label="Agent portrait"></div>
<div class="portrait" style="left:860px;top:1420px;width:133px;height:127px" role="img" aria-label="Agent portrait"></div>
<div class="portrait" style="left:1006px;top:1218px;width:133px;height:128px" role="img" aria-label="Agent portrait"></div>
<div class="portrait" style="left:1006px;top:1357px;width:133px;height:128px" role="img" aria-label="Agent portrait"></div>

<!-- Listings -->
<div class="abs h2" style="left:0;width:1200px;text-align:center;top:1676px">Listings Available For Latest Property</div>
<div class="abs" style="left:510px;top:1722px;width:180px;height:2px;background:var(--gold)"></div>
<div class="tab on" style="left:293px;width:102px">For Sale</div>
<div class="tab" style="left:418px;width:107px">For Lease</div>
<div class="tab" style="left:545px;width:107px">Open Times</div>
<div class="tab" style="left:673px;width:106px">Sold</div>
<div class="tab" style="left:800px;width:106px">Leased</div>

<article class="card" style="left:60px">
  <div class="card-head"><svg class="abs" style="left:18px;top:10px" width="20" height="24" viewBox="0 0 20 24" fill="none" stroke="#fff" stroke-width="1.6"><path d="M10 22s7-7 7-12a7 7 0 0 0-14 0c0 5 7 12 7 12z"/><circle cx="10" cy="10" r="2.5"/></svg><b>Gungahlin</b><br>Level 5/71/1 Harlow Crescent…<svg class="abs" style="right:14px;top:10px" width="22" height="22" viewBox="0 0 24 24"><path d="M12 2l3 7 7 .6-5.4 4.6 1.7 7.3L12 17.6 5.7 21.5l1.7-7.3L2 9.6 9 9z" fill="#ecbd4f"/></svg></div>
  <div class="card-photo" role="img" aria-label="Apartment building beside a tree" style="background:linear-gradient(160deg,#c9d6e4,#e6e1dc 45%,#5c6a4e 80%)"><span class="price">$369,900+</span></div>
  <div class="card-specs"><span>▭ 2</span><span>◡ 2</span><span>⊡ 1</span></div>
  <div class="ins">Next Inspection:</div><div class="date">Sat 21st May 9:40 Am-10:00 Am</div>
  <div class="foot"><div class="avatar"></div>Mei Lin<span style="margin-left:auto;letter-spacing:8px">◷⤢✉</span></div>
</article>
<article class="card" style="left:430px">
  <div class="card-head"><svg class="abs" style="left:18px;top:10px" width="20" height="24" viewBox="0 0 20 24" fill="none" stroke="#fff" stroke-width="1.6"><path d="M10 22s7-7 7-12a7 7 0 0 0-14 0c0 5 7 12 7 12z"/><circle cx="10" cy="10" r="2.5"/></svg><b>Gungahlin</b><br>Level 5/71/1 Harlow Crescent…<svg class="abs" style="right:14px;top:10px" width="22" height="22" viewBox="0 0 24 24"><path d="M12 2l3 7 7 .6-5.4 4.6 1.7 7.3L12 17.6 5.7 21.5l1.7-7.3L2 9.6 9 9z" fill="#ecbd4f"/></svg></div>
  <div class="card-photo" role="img" aria-label="Rooftop pool with city view" style="background:linear-gradient(170deg,#d9dde2,#9fb4c6 45%,#3d6fb8 75%,#2b57a0)"><span class="price">$5,00,000+</span></div>
  <div class="card-specs"><span>▭ 2</span><span>◡ 2</span><span>⊡ 1</span></div>
  <div class="ins">Next Inspection:</div><div class="date">Sat 21st May 9:40 Am-10:00 Am</div>
  <div class="foot"><div class="avatar"></div>Mei Lin<span style="margin-left:auto;letter-spacing:8px">◷⤢✉</span></div>
</article>
<article class="card" style="left:800px">
  <div class="card-head"><svg class="abs" style="left:18px;top:10px" width="20" height="24" viewBox="0 0 20 24" fill="none" stroke="#fff" stroke-width="1.6"><path d="M10 22s7-7 7-12a7 7 0 0 0-14 0c0 5 7 12 7 12z"/><circle cx="10" cy="10" r="2.5"/></svg><b>Gungahlin</b><br>Level 5/71/1 Harlow Crescent…<svg class="abs" style="right:14px;top:10px" width="22" height="22" viewBox="0 0 24 24"><path d="M12 2l3 7 7 .6-5.4 4.6 1.7 7.3L12 17.6 5.7 21.5l1.7-7.3L2 9.6 9 9z" fill="#ecbd4f"/></svg></div>
  <div class="card-photo" role="img" aria-label="Suburban house with double garage" style="background:linear-gradient(170deg,#cfd9e3,#7d7a68 40%,#b49a80 75%,#c9b59c)"><span class="price">$5,00,000+</span></div>
  <div class="card-specs"><span>▭ 2</span><span>◡ 2</span><span>⊡ 1</span></div>
  <div class="ins">Next Inspection:</div><div class="date">Sat 21st May 9:40 Am-10:00 Am</div>
  <div class="foot"><div class="avatar"></div>Mei Lin<span style="margin-left:auto;letter-spacing:8px">◷⤢✉</span></div>
</article>
<div class="btn" style="left:546px;top:2263px;width:102px;height:34px">View More</div>

<!-- Testimonials -->
<section class="abs quotes"></section>
<div class="abs h2" style="left:0;top:2425px;width:1200px;text-align:center;color:var(--white)">What Our People Says</div>
<div class="abs" style="left:355px;top:2480px;font-size:54px;color:#3f6fb0;font-style:italic">“</div>
<p class="abs" style="left:370px;top:2511px;width:460px;text-align:center;font-style:italic;font-size:13.5px;line-height:22.6px;color:var(--white)">"They are a greatly professional, organized and experienced team with extensive knowledge and understanding of the local market. My husband and I were provided with excellent feedback in a simple language we could understand and advice throughout the house journey and we were very pleased with the results. We highly recommend Ferndale Estate Collective to anyone buying, selling or in need of property management in the local area."</p>
<div class="abs" style="left:0;width:1200px;text-align:center;top:2690px;font-size:13px;color:var(--gold)">Rosa Whitfield</div>
<div class="arrow" style="left:146px;background:var(--gold)"><svg width="22" height="12" viewBox="0 0 22 12"><path d="M21 6H2M7 1L2 6l5 5" fill="none" stroke="#1b3358" stroke-width="1.8"/></svg></div>
<div class="arrow" style="left:1005px;background:var(--white)"><svg width="22" height="12" viewBox="0 0 22 12"><path d="M1 6h19M15 1l5 5-5 5" fill="none" stroke="#1b3358" stroke-width="1.8"/></svg></div>

<!-- News -->
<div class="abs h2" style="left:0;top:2830px;width:1200px;text-align:center">Our Latest News</div>
<div class="abs" style="left:545px;top:2876px;width:110px;height:2px;background:var(--gold)"></div>

<div class="news-photo" style="left:60px;top:2912px;background:linear-gradient(120deg,#d6dde4,#8a6a4e 60%,#5a3e2c)" role="img" aria-label="Living room with timber floors"></div>
<div class="meta" style="left:317px;top:2920px">▦ 8 March 2022 &nbsp;&nbsp; ◌ 5 Comments</div>
<div class="news-title" style="left:317px;top:2947px">Lorem Ipsum is simply dummy text</div>
<div class="read" style="left:317px;top:3027px">Read More ⟶</div>

<div class="news-photo" style="left:598px;top:2912px;background:linear-gradient(120deg,#e6e2dc,#c9bfae 60%,#6b6660)" role="img" aria-label="Modern kitchen"></div>
<div class="meta" style="left:860px;top:2920px">▦ 8 March 2022 &nbsp;&nbsp; ◌ 5 Comments</div>
<div class="news-title" style="left:860px;top:2947px">Lorem Ipsum is simply dummy text</div>
<div class="read" style="left:860px;top:3027px">Read More ⟶</div>

<div class="news-photo" style="left:60px;top:3087px;background:linear-gradient(120deg,#eeeeec,#cfcfcb 55%,#9b9180)" role="img" aria-label="Empty open-plan room"></div>
<div class="meta" style="left:317px;top:3096px">▦ 8 March 2022 &nbsp;&nbsp; ◌ 5 Comments</div>
<div class="news-title" style="left:317px;top:3123px">Lorem Ipsum is simply dummy text</div>
<div class="read" style="left:317px;top:3202px">Read More ⟶</div>

<div class="news-photo" style="left:598px;top:3087px;background:linear-gradient(175deg,#6e9ed8,#b6c9dc 35%,#8a4a3a 60%,#5f7d4a)" role="img" aria-label="Brick house under blue sky"></div>
<div class="meta" style="left:860px;top:3096px">▦ 8 March 2022 &nbsp;&nbsp; ◌ 5 Comments</div>
<div class="news-title" style="left:860px;top:3123px">Lorem Ipsum is simply dummy text</div>
<div class="read" style="left:860px;top:3202px">Read More ⟶</div>

<!-- CTA -->
<section class="abs cta"></section>
<div class="abs" style="left:0;top:3362px;width:1200px;text-align:center;font-size:24px;line-height:34px;font-weight:500;color:var(--white)">Contact Us If You Want To Sell Your House Or You<br>Have Other Questions</div>
<div class="abs" style="left:496px;top:3456px;width:207px;height:33px;background:var(--navy);color:var(--white);font-size:13px;display:flex;align-items:center;justify-content:center;border:2px solid var(--white)">Request Free Consultation</div>

<!-- Footer -->
<footer class="abs footer">
  <div class="abs" style="left:60px;top:34px;display:flex;align-items:center;gap:10px">
    <div style="width:52px;height:52px;border:3px solid var(--white)"></div>
    <div><div style="font-size:38px;font-weight:500;line-height:1">Ferndale</div><div style="font-size:10px;letter-spacing:1px;margin-top:3px">Estate Collective</div></div>
  </div>
  <p class="abs" style="left:60px;top:118px;width:200px;font-size:12px;line-height:22px">Lorem ipsum dolor sit amet, consectetur adipiscing elit, sed do eiusmod tempor...</p>
  <h4 style="left:329px;top:48px">Site Map</h4>
  <ul style="left:325px;top:86px"><li>Home</li><li>About Us</li><li>Leasing</li><li>Buy</li><li>Sell</li><li>Our Team</li><li>Blog</li><li>Contact Us</li></ul>
  <h4 style="left:613px;top:48px">Contact Us</h4>
  <svg class="abs" style="left:611px;top:88px" width="20" height="24" viewBox="0 0 20 24" fill="none" stroke="#fff" stroke-width="1.5"><path d="M10 22s7-7 7-12a7 7 0 0 0-14 0c0 5 7 12 7 12z"/><circle cx="10" cy="10" r="2.5"/></svg>
  <div class="abs" style="left:644px;top:88px;font-size:12px;line-height:20px;width:220px">18/4 Harlow Crescent, Gungahlin<br>, ACT, 2912</div>
  <svg class="abs" style="left:611px;top:136px" width="20" height="20" viewBox="0 0 20 20" fill="none" stroke="#fff" stroke-width="1.5"><path d="M4 2l4 1 1 4-2 2a11 11 0 0 0 4 4l2-2 4 1 1 4-3 2C8 18 2 12 2 5z"/></svg>
  <div class="abs" style="left:648px;top:136px;font-size:12px;line-height:24px;font-weight:600">02 6100 4821<br>02 6100 4937</div>
  <svg class="abs" style="left:611px;top:200px" width="22" height="16" viewBox="0 0 22 16" fill="none" stroke="#fff" stroke-width="1.5"><rect x="1" y="1" width="20" height="14"/><path d="M1 1l10 8 10-8"/></svg>
  <div class="abs" style="left:644px;top:198px;font-size:12px">info@ferndaleestate.com.au</div>
  <h4 style="left:889px;top:48px">Follow On Us</h4>
  <div class="abs" style="left:0;top:302px;width:1200px;height:1px;background:rgba(255,255,255,.25)"></div>
  <div class="abs" style="left:60px;top:316px;font-size:12px">2022© Ferndale Estate Collective. All right reserved.</div>
  <div class="abs" style="left:655px;top:316px;font-size:12px;display:flex;gap:26px"><span>Privacy</span><span>Complaint Handling &amp; Dispute Resolution</span><span>Due Diligence Checklist</span></div>
</footer>
<div class="social" style="left:888px;background:var(--gold);border-color:var(--gold)" aria-label="Social link"></div>
<div class="social" style="left:942px" aria-label="Social link"></div>
<div class="social" style="left:998px" aria-label="Social link"></div>
<div class="social" style="left:1051px" aria-label="Social link"></div>

</body>
</html>
```